Brightfield Learning Enrichment Academy

We need a signage design for our Brightfield Learning Academic Enrichment Academy. We provide tutoring and enrichment to students grades 1-8 in math, science and reading, and also give life skills. We also provide quarterly community services initiatives and athletic skills clinics.
We want to be the place that parents can take their kids that need tutoring, enrichment, or sharpen their skills for the next academic school year. Our program has been in existence since 2012, and we are moving into our first facility. We want something that stands out from the busy street that our building is located on.
Please visit www.brightfieldlearners.org for more information on our organization.
Using the letters acronym B.L.E in a favorable fashion would be fantastic if at all possible
Thanks.

Target Market(s)

Parents with students in grades 1st-8th
Students who seek to prepare for grade level enrichment
Grant providers who seek reputable programs that are actually doing the work of mentoring, tutoring students

Industry/Entity Type

Tutoring

Font styles to use
Other font styles liked:
• the collegiate font

Colors
0255a3
85acd3
cee9f5

Requirements
Must have
• B.L.E as some form of acronym
Should not have
• N/A

```html
<!DOCTYPE html>
<html lang="en">
<head>
<meta charset="utf-8">
<title>Brightfield Learning Enrichment Academy – Signage</title>
<link href="https://fonts.googleapis.com/css2?family=Montserrat:wght@700;800&display=swap" rel="stylesheet">
<style>
  :root {
    --brand-blue: #0255a3;
    --mid-blue: #85acd3;
    --ice-blue: #cee9f5;
    --white: #ffffff;
    --backdrop: #eef2f6;
  }
  html, body {
    margin: 0;
    padding: 0;
    width: 1200px;
    height: 900px;
    overflow: hidden;
    background: var(--backdrop);
  }
  .sign {
    position: absolute;
    left: 50px;
    top: 150px;
    width: 1100px;
    height: 600px;
    box-sizing: border-box;
    background: var(--brand-blue);
    border: 12px solid var(--white);
    font-family: "Montserrat", Arial, sans-serif;
    color: var(--white);
  }
  .logo-art {
    position: absolute;
    left: 60px;
    top: 60px;
    width: 420px;
    height: 330px;
    background: linear-gradient(180deg, var(--ice-blue) 0%, var(--mid-blue) 100%);
  }
  .logo-name {
    position: absolute;
    left: 60px;
    top: 398px;
    width: 420px;
    display: flex;
    align-items: center;
    gap: 10px;
    font-weight: 800;
    font-size: 26px;
    letter-spacing: 3px;
    color: var(--ice-blue);
    white-space: nowrap;
  }
  .logo-name .mark {
    width: 16px;
    height: 16px;
    background: var(--ice-blue);
    flex: none;
  }
  .headline {
    position: absolute;
    left: 515px;
    top: 120px;
    margin: 0;
    font-weight: 800;
    font-size: 70px;
    line-height: 1.05;
    letter-spacing: 1px;
    text-transform: uppercase;
  }
  .headline span { display: block; }
  .services {
    position: absolute;
    left: 60px;
    right: 30px;
    top: 460px;
    margin: 0;
    padding: 0;
    list-style: none;
    display: flex;
    align-items: center;
    font-weight: 800;
    font-size: 38px;
    letter-spacing: 2px;
    text-transform: uppercase;
    white-space: nowrap;
  }
  .services li { display: flex; align-items: center; }
  .services li::before {
    content: "";
    width: 12px;
    height: 12px;
    border-radius: 50%;
    background: var(--mid-blue);
    margin: 0 10px 0 6px;
  }
</style>
</head>
<body>
  <main class="sign">
    <div class="logo-art" role="img" aria-label="Light blue city skyline with three graduates in caps and gowns"></div>
    <div class="logo-name"><span class="mark"></span>B.L.E</div>
    <h1 class="headline">
      <span>Brightfield</span>
      <span>Learning</span>
      <span>Enrichment</span>
    </h1>
    <ul class="services">
      <li>Tutoring</li>
      <li>Enrichment</li>
      <li>Sharpen Skills</li>
    </ul>
  </main>
</body>
</html>
```